Women's health flyer for Vindbro Health & Wellness . for a Women's health conference

I need a flyer , post card 4x 6 or 5 x 7 sized designed , 2 sides focused on my business branding and Women's health. we deliver bespoke care and focus on all phases of women's health and life. I want something aligned with our bespoke whole person care philosophy and that is fresh and forward thinking.
www.vindbro-care.com
This is to help women know they can have care for all phases of life , fertility , postpartum , perimenopause , mental health , wellness, weight loss, increased energy stress , menopause etc
please use knowledge from website about my company , www.vindbro-care.com
I also feel like my brand kit could use an additional secondarily color option in it

Target Market(s)

Women 25-70

Industry/Entity Type

health & Wellness

Colors
0054AA
0677BA
7BADD7
CADEEF
E8F1F8
0094D4
00A9DD
6FCCEA
C7EBF8
E9F6FB
00AB8E
00BBA5
67D7C9
C6EFE9
E9F9F6
59FF00
82FF00
B8FF75
E3FFCB
F4FFEA
E54698
E96AAD
F1A4CE
F9D9EA
FCEFF6
A7469A
B969AE
D3A5CF
EDDBEB
F8F0F9

Requirements
Must have
• photos , my logo, connection to my brand
Nice to have
• something fresh and different
Should not have
• look like a genetic "wellness program"

```html
<!DOCTYPE html>
<html lang="en">
<head>
<meta charset="utf-8">
<title>Vindbro Health &amp; Wellness – Women's Health Postcard</title>
<link rel="stylesheet" href="https://fonts.googleapis.com/css2?family=Montserrat:ital,wght@0,400;0,500;0,600;0,700;0,800;1,400&display=swap">
<style>
  :root {
    --brand-green: #6ab000;
    --brand-blue: #0677ba;
    --brand-deep: #0a5d8c;
    --sky-blue: #1a9fd0;
    --ink: #2b2b2b;
    --paper: #ffffff;
    --rule: #6ab000;
    --dot: #6d6d6d;
  }
  * { box-sizing: border-box; margin: 0; padding: 0; }
  html, body { width: 849px; height: 1200px; overflow: hidden; background: var(--paper); }
  body { position: relative; font-family: "Montserrat", Arial, sans-serif; color: var(--ink); }

  .card {
    position: absolute; left: 93px; width: 663px; height: 472px;
    background: var(--paper); overflow: hidden;
    box-shadow: 0 4px 10px rgba(0,0,0,0.35);
  }
  .card--front { top: 70px; }
  .card--back { top: 659px; }
  .card__art { position: absolute; inset: 0; width: 663px; height: 472px; }

  .brand { position: absolute; color: var(--brand-deep); font-weight: 600; text-align: center; line-height: 1; }
  .brand__name { display: block; letter-spacing: 1px; }
  .brand__tag { display: block; letter-spacing: 2.4px; margin-top: 3px; color: var(--brand-deep); }
  .brand__dot { display: block; width: 14px; height: 14px; border-radius: 50%; background: var(--sky-blue); margin: 0 auto 6px; }
  .card--front .brand { right: 16px; top: 36px; width: 110px; }
  .card--front .brand__name { font-size: 20px; }
  .card--front .brand__tag { font-size: 5.6px; }
  .card--back .brand { left: 29px; top: 48px; text-align: left; }
  .card--back .brand__name { font-size: 27px; }
  .card--back .brand__tag { font-size: 7.4px; letter-spacing: 3.6px; margin-top: 4px; }

  .profile { position: absolute; left: 343px; top: 130px; width: 282px; }
  .profile__name { font-size: 13.4px; font-weight: 700; color: var(--brand-green); letter-spacing: 0.1px; white-space: nowrap; }
  .profile__label { font-size: 7.6px; font-weight: 500; color: var(--brand-blue); margin: 9px 0 0 3px; }
  .profile__bio { font-size: 9.8px; line-height: 12.8px; margin: 8px 0 0 1px; width: 272px; }
  .profile__rule { height: 1px; background: var(--rule); margin: 12px 0 0 1px; width: 267px; }

  .contacts { list-style: none; position: absolute; left: 343px; top: 390px; font-size: 9.4px; font-style: italic; letter-spacing: 0.7px; line-height: 11.6px; }
  .contacts li { display: flex; align-items: flex-start; }
  .contacts svg { width: 7px; height: 7px; margin: 2px 8px 0 0; flex: none; fill: var(--brand-blue); }

  .scene-photo { position: absolute; left: 29px; top: 94px; width: 312px; height: 135px;
    background: linear-gradient(180deg, #9cc3e6 0%, #dfe9f2 38%, #3f5b3c 48%, #6e7d4a 62%, #a9bccf 78%, #8a8f7e 100%);
    box-shadow: 4px 4px 6px rgba(0,0,0,0.4); }

  .write-lines { position: absolute; left: 374px; width: 241px; top: 0; }
  .write-lines span { position: absolute; left: 0; width: 241px; border-top: 1.2px dotted var(--dot); }

  .why__title { position: absolute; left: 29px; top: 254px; font-size: 22.5px; font-weight: 800; color: #fff; }
  .features { position: absolute; left: 20px; top: 289px; width: 628px; display: flex; }
  .feature { width: 157px; text-align: center; color: #fff; padding: 0 9px; }
  .feature__icon { width: 31px; height: 31px; margin: 0 auto; background: #fff; border: 1.2px solid var(--brand-blue); display: flex; align-items: center; justify-content: center; }
  .feature__icon svg { width: 22px; height: 22px; fill: none; stroke: var(--brand-green); stroke-width: 1.3; stroke-linecap: round; stroke-linejoin: round; }
  .feature__title { font-size: 9px; font-weight: 600; line-height: 10.8px; margin-top: 7px; min-height: 22px; }
  .feature__text { font-size: 6.3px; line-height: 8.5px; margin-top: 6px; }
</style>
</head>
<body>

<section class="card card--front">
  <svg class="card__art" viewBox="0 0 663 472" aria-hidden="true">
    <defs>
      <linearGradient id="band" x1="0" y1="0" x2="0" y2="1">
        <stop offset="0" stop-color="#6ab000"/>
        <stop offset="0.55" stop-color="#6ab000"/>
        <stop offset="0.62" stop-color="#1a9fd0"/>
        <stop offset="1" stop-color="#0677ba"/>
      </linearGradient>
    </defs>
    <rect width="663" height="472" fill="url(#band)"/>
    <path d="M323 0 H663 V472 H254 C234 400 238 320 262 240 C284 170 312 90 323 0 Z" fill="#fff"/>
  </svg>
  <svg class="card__art" viewBox="0 0 663 472" role="img" aria-label="Photo of the practitioner in flowing white clothing, arms raised before a large rock and blue sky">
    <defs>
      <linearGradient id="portrait" x1="0" y1="0" x2="1" y2="1">
        <stop offset="0" stop-color="#a9c6e4"/>
        <stop offset="0.4" stop-color="#c2a07d"/>
        <stop offset="0.7" stop-color="#e9eaee"/>
        <stop offset="1" stop-color="#6d5a48"/>
      </linearGradient>
    </defs>
    <path d="M0 0 H284 C290 90 270 160 248 230 C226 300 212 390 216 472 H0 Z" fill="url(#portrait)"/>
  </svg>

  <div class="brand">
    <span class="brand__dot"></span>
    <span class="brand__name">VINDBRO</span>
    <span class="brand__tag">HEALTH &amp; WELLNESS</span>
  </div>

  <div class="profile">
    <h1 class="profile__name">DR MAREN L OSTWICK DACM, L.AC.</h1>
    <h2 class="profile__label">ABOUT ME</h2>
    <p class="profile__bio">From a young age, Traditional East Asian Medicine (T.E.A.M) played a pivotal role in overcoming significant lung concerns, allowing me to pursue my aspirations as a young athlete. This early encounter sparked a lifelong dedication to healing women and prompted a deep exploration of how best to serve my community. Today I offer bespoke care for every phase of a woman's life: fertility, postpartum, perimenopause, menopause, mental health, stress, energy and weight. My journey into healthcare began after seven years of creativity and leadership in theatre costume design, inspiring me to blend art and science in Acupuncture and Traditional East Asian Medicine (T.E.A.M).</p>
    <div class="profile__rule"></div>
  </div>

  <ul class="contacts">
    <li><svg viewBox="0 0 10 10"><path d="M2 0.5 L3.6 2.6 L2.8 3.6 C3.4 5 4.8 6.4 6.3 7.1 L7.3 6.3 L9.5 7.9 L8.4 9.5 C4.6 9.3 0.7 5.4 0.5 1.6 Z"/></svg>+1-555-014-2290</li>
    <li><svg viewBox="0 0 10 10"><circle cx="5" cy="5" r="4.3" fill="none" stroke="#0677ba" stroke-width="1"/><path d="M0.7 5 H9.3 M5 0.7 C2.5 3 2.5 7 5 9.3 C7.5 7 7.5 3 5 0.7" fill="none" stroke="#0677ba" stroke-width="0.9"/></svg>www.vindbro-care.com</li>
    <li><svg viewBox="0 0 10 10"><path d="M0.5 2 H9.5 V8.5 H0.5 Z"/><path d="M0.8 2.3 L5 5.6 L9.2 2.3" fill="none" stroke="#fff" stroke-width="0.9"/></svg>maren@ostwickcare.com</li>
    <li><svg viewBox="0 0 10 10"><path d="M5 0.5 C7.4 0.5 8.6 2.2 8.6 4 C8.6 6.2 5 9.5 5 9.5 C5 9.5 1.4 6.2 1.4 4 C1.4 2.2 2.6 0.5 5 0.5 Z"/><circle cx="5" cy="3.9" r="1.3" fill="#fff"/></svg>412 Alder Lane Fairview, MO,<br>64000</li>
  </ul>
</section>

<section class="card card--back">
  <svg class="card__art" viewBox="0 0 663 472" aria-hidden="true">
    <path d="M0 183 C200 222 420 272 560 262 C615 258 645 250 663 243 V472 H0 Z" fill="#0a5d8c"/>
    <path d="M0 183 C200 226 420 280 560 276 C615 274 645 272 663 271 V472 H0 Z" fill="#6ab000"/>
  </svg>

  <div class="brand">
    <span class="brand__name">VINDBRO</span>
    <span class="brand__tag">HEALTH &amp; WELLNESS</span>
  </div>

  <div class="scene-photo" role="img" aria-label="Photo of a wooden boardwalk crossing a wetland pond reflecting clouds, with a line of pine trees"></div>

  <div class="write-lines">
    <span style="top:151px"></span>
    <span style="top:188px"></span>
    <span style="top:227px"></span>
  </div>

  <h2 class="why__title">Why Choose Us</h2>

  <div class="features">
    <article class="feature">
      <div class="feature__icon"><svg viewBox="0 0 24 24"><path d="M3 15 H7 L11 17 H16 C17 17 17 19 16 19 H10"/><path d="M3 21 H13 L20 16 C21 15 20 13.5 19 14 L15 16"/><path d="M8 10 H10 L11.5 7 L13 12 L14.5 9 H17"/><circle cx="18" cy="5" r="2.5"/><path d="M18 3.8 V6.2 M16.8 5 H19.2"/></svg></div>
      <h3 class="feature__title">Whole Person<br>Approach</h3>
      <p class="feature__text">Vindbro combines Traditional Eastern Medicine (T.E.A.M) with modern practices to care for women in every phase of life, from fertility and postpartum to perimenopause and menopause. We honor the connection of mind, body and spirit, truly treating the whole woman.</p>
    </article>
    <article class="feature">
      <div class="feature__icon"><svg viewBox="0 0 24 24"><path d="M12 5 C9.5 8 9.5 13 12 17 C14.5 13 14.5 8 12 5 Z"/><path d="M12 17 C8.5 16 6.5 12 7 8.5 C9 9.5 10.5 11 11 13"/><path d="M12 17 C15.5 16 17.5 12 17 8.5 C15 9.5 13.5 11 13 13"/><path d="M12 17 C8 18 4 15.5 3 12 C5 11.5 7 12 8.5 13"/><path d="M12 17 C16 18 20 15.5 21 12 C19 11.5 17 12 15.5 13"/></svg></div>
      <h3 class="feature__title">Comprehensive<br>Support</h3>
      <p class="feature__text">Vindbro is committed to helping women thrive with bespoke, comprehensive support. We offer clear, actionable skills for daily living and rooted care for mental health, stress, weight loss and renewed energy. Every woman gains guidance that lifts her quality of life and fosters lasting change.</p>
    </article>
    <article class="feature">
      <div class="feature__icon"><svg viewBox="0 0 24 24"><path d="M8 21 V17 C5 15.5 4 12.5 4.5 10 C5.5 5 9.5 3 13 3 C17 3 20 6 20 10 C20 12 19 13.5 18 14.5 V18 H15 V21"/><path d="M12 13 C9 11 9 8 11 8 C11.8 8 12 8.8 12 8.8 C12 8.8 12.2 8 13 8 C15 8 15 11 12 13 Z"/></svg></div>
      <h3 class="feature__title">Revolutionary Designed<br>Programs</h3>
      <p class="feature__text">Vindbro integrates evidence-based research, established theories and innovative ideas to create forward-thinking women's health programs that meet the changing needs of each life phase. By blending these elements, our care is grounded in proven methods while embracing new insights for fertility, hormonal balance and menopause. This approach enhances the effectiveness of our services, fosters continuous innovation, and helps us deliver the best possible outcomes for every woman's well-being and growth.</p>
    </article>
    <article class="feature">
      <div class="feature__icon"><svg viewBox="0 0 24 24"><circle cx="12" cy="7" r="2"/><path d="M12 9 V21"/><path d="M12 14 C9 13 5 10 4 6 C7 6 10 9 12 12"/><path d="M12 14 C15 13 19 10 20 6 C17 6 14 9 12 12"/><path d="M12 18 C9 18 6 16.5 5 14"/><path d="M12 18 C15 18 18 16.5 19 14"/><path d="M9 4 C10 2.5 14 2.5 15 4"/></svg></div>
      <h3 class="feature__title">Community and<br>Individuality</h3>
      <p class="feature__text">Inspired by ships charting their own course across the ocean, Vindbro honors each woman's individual needs within a caring community. From ages 25 to 70, our clients feel valued, understood and empowered to pursue personal growth and healing through every season of life.</p>
    </article>
  </div>
</section>

</body>
</html>
```